Womans Supplement Designs

Launching a Supplement company and need to get some initial designs created, I've attached our logo and the bottle type that I want the samples done one.

This project is for our Whey Protein we are starting with Vanilla, chocolate and strawberry banana

(ALL DESIGN VARIATIONS MUST BE A WHITE BOTTLE NOT BLACK)

(FOR DESIGN SAMPLES PLEASE USE THE SUPPLEMENT BOTTLE STYLE I PROVIDED)

Whoever is selected the winner I will have more work for you to complete the disigns for the rest of the products in the line, Just want to get this shake completed first

Target Market(s)

Women

Requirements
Must have
• Must have our current logo involved

the name of this product will be "RUNE MOSA"

Must have this slogan,

ALL-IN-ONE PREMIUM PROTEIN NUTRITIONAL SHAKE FOR BLACK WOMEN

This is our meal replacement

the design should try to keep the same look and feel of the existing provided supplement images

we are starting with chocolate, vanilla and strawberry banana

this is for women and should look colorful and appeal to them
Should not have
• Do not use an image of a person or lady, don't want it branded to a person

```html
<!DOCTYPE html>
<html lang="en">
<head>
<meta charset="utf-8">
<title>RUNE MOSA Whey Protein Labels</title>
<link href="https://fonts.googleapis.com/css2?family=Archivo+Black&family=Poppins:ital,wght@0,600;0,700;1,700&display=swap" rel="stylesheet">
<style>
  :root {
    --page-bg: #f3f3f3;
    --label-black: #000000;
    --label-white: #ffffff;
    --title-pink: #f04c9e;
    --panel-grey: #c9c9c9;
    --choc: #c4522a;
    --berry: #c4260f;
    --vanilla: #e8900e;
  }
  html, body {
    margin: 0;
    padding: 0;
    width: 1200px;
    height: 3127px;
    overflow: hidden;
    background: var(--page-bg);
  }
  .label {
    position: absolute;
    left: 0;
    width: 1200px;
    height: 923px;
    display: block;
  }
  .label--chocolate { top: 73px; }
  .label--strawberry-banana { top: 1083px; }
  .label--vanilla { top: 2110px; }

  .brand-name { font-family: "Poppins", sans-serif; font-weight: 600; font-size: 30px; letter-spacing: 5px; fill: var(--label-black); }
  .brand-name--side { font-size: 18px; letter-spacing: 2px; fill: var(--label-white); }
  .product-title { font-family: "Archivo Black", sans-serif; font-size: 128px; fill: var(--title-pink); stroke: var(--label-white); stroke-width: 9px; paint-order: stroke; }
  .slogan { font-family: "Poppins", sans-serif; font-style: italic; font-weight: 700; font-size: 24px; fill: var(--label-white); }
  .slogan--boxed { fill: var(--label-black); }
  .protein-type { font-family: "Poppins", sans-serif; font-weight: 700; font-size: 24px; fill: var(--label-white); }
  .net-weight { font-family: "Poppins", sans-serif; font-weight: 600; font-size: 30px; fill: var(--label-white); }
  .band-text { font-family: "Poppins", sans-serif; font-style: italic; font-weight: 700; font-size: 33px; fill: var(--label-white); }
  .flavour-name { font-family: "Poppins", sans-serif; font-weight: 700; font-size: 40px; }
  .label--chocolate .flavour-name { fill: var(--choc); }
  .label--strawberry-banana .flavour-name { fill: var(--berry); font-size: 32px; }
  .label--vanilla .flavour-name { fill: var(--vanilla); }
</style>
</head>
<body>

<!-- Chocolate -->
<svg class="label label--chocolate" viewBox="0 0 988 760" xmlns="http://www.w3.org/2000/svg">
  <defs>
    <linearGradient id="topfade-c" x1="0" y1="0" x2="0" y2="1"><stop offset="0.4" stop-color="#fff"/><stop offset="0.78" stop-color="#000"/></linearGradient>
    <linearGradient id="arm-c" gradientUnits="userSpaceOnUse" x1="988" y1="110" x2="520" y2="745"><stop offset="0" stop-color="#111"/><stop offset="0.5" stop-color="#fff"/></linearGradient>
    <linearGradient id="fig-c" x1="0" y1="0" x2="1" y2="1"><stop offset="0" stop-color="#555"/><stop offset="0.5" stop-color="#111"/><stop offset="1" stop-color="#333"/></linearGradient>
    <linearGradient id="flav-c" x1="0" y1="0" x2="0" y2="1"><stop offset="0.3" stop-color="#c9c9c9"/><stop offset="0.6" stop-color="#7a3a22"/><stop offset="1" stop-color="#3d1a0e"/></linearGradient>
  </defs>
  <rect width="988" height="760" fill="var(--label-black)"/>
  <polygon points="267,0 720,0 494,470" fill="url(#topfade-c)"/>
  <rect x="0" y="0" width="180" height="760" fill="url(#fig-c)" role="img" aria-label="Silhouette of a woman"/>
  <rect x="446" y="210" width="58" height="80" rx="10" fill="#0a0a0a" role="img" aria-label="Small figure silhouette"/>
  <polygon points="570,760 988,208 988,760" fill="var(--panel-grey)"/>
  <polygon points="660,760 988,330 988,760" fill="url(#flav-c)" role="img" aria-label="Chocolate shake pouring with chocolate pieces"/>
  <polygon points="570,760 988,208 988,318 650,760" fill="var(--choc)"/>
  <polygon class="w-shape" points="182,398 235,380 418,665 460,608 494,650 530,608 570,665 988,113 988,208 570,760 558,760 494,640 430,760 415,760" fill="url(#arm-c)"/>
  <text class="brand-name" x="494" y="170" text-anchor="middle">NOVA ROOT</text>
  <text class="brand-name brand-name--side" x="93" y="400" text-anchor="middle">NOVA ROOT</text>
  <text class="product-title" x="497" y="388" text-anchor="middle" textLength="525" lengthAdjust="spacingAndGlyphs">RUNE MOSA</text>
  <text class="slogan" x="493" y="457" text-anchor="middle">ALL-IN-ONE PREMIUM PROTEIN</text>
  <text class="slogan" x="493" y="486" text-anchor="middle">NUTRITIONAL SHAKE</text>
  <rect x="363" y="493" width="259" height="27" fill="var(--label-white)"/>
  <text class="slogan slogan--boxed" x="492" y="515" text-anchor="middle">FOR BLACK WOMEN</text>
  <text class="protein-type" x="488" y="592" text-anchor="middle">WHEY PROTEIN</text>
  <text class="net-weight" x="492" y="738" text-anchor="middle">750g</text>
  <text class="band-text" transform="translate(792,545) rotate(-52.8)" text-anchor="middle">THIS IS OUR MEAL REPLACEMENT</text>
  <text class="flavour-name" transform="translate(972,505) rotate(-90)" text-anchor="middle">chocolate</text>
</svg>

<!-- Strawberry banana -->
<svg class="label label--strawberry-banana" viewBox="0 0 988 760" xmlns="http://www.w3.org/2000/svg">
  <defs>
    <linearGradient id="topfade-s" x1="0" y1="0" x2="0" y2="1"><stop offset="0.4" stop-color="#fff"/><stop offset="0.78" stop-color="#000"/></linearGradient>
    <linearGradient id="arm-s" gradientUnits="userSpaceOnUse" x1="988" y1="110" x2="520" y2="745"><stop offset="0" stop-color="#111"/><stop offset="0.5" stop-color="#fff"/></linearGradient>
    <linearGradient id="fig-s" x1="0" y1="0" x2="1" y2="1"><stop offset="0" stop-color="#555"/><stop offset="0.5" stop-color="#111"/><stop offset="1" stop-color="#333"/></linearGradient>
    <linearGradient id="flav-s" x1="0" y1="0" x2="0" y2="1"><stop offset="0.3" stop-color="#c9c9c9"/><stop offset="0.6" stop-color="#f4c7cf"/><stop offset="0.85" stop-color="#f2d98a"/><stop offset="1" stop-color="#e7a0a8"/></linearGradient>
  </defs>
  <rect width="988" height="760" fill="var(--label-black)"/>
  <polygon points="267,0 720,0 494,470" fill="url(#topfade-s)"/>
  <rect x="0" y="0" width="180" height="760" fill="url(#fig-s)" role="img" aria-label="Silhouette of a woman"/>
  <rect x="446" y="210" width="58" height="80" rx="10" fill="#0a0a0a" role="img" aria-label="Small figure silhouette"/>
  <polygon points="570,760 988,208 988,760" fill="var(--panel-grey)"/>
  <polygon points="660,760 988,330 988,760" fill="url(#flav-s)" role="img" aria-label="Strawberry and banana slices splashing in pink milk"/>
  <polygon points="570,760 988,208 988,318 650,760" fill="var(--berry)"/>
  <polygon class="w-shape" points="182,398 235,380 418,665 460,608 494,650 530,608 570,665 988,113 988,208 570,760 558,760 494,640 430,760 415,760" fill="url(#arm-s)"/>
  <text class="brand-name" x="494" y="170" text-anchor="middle">NOVA ROOT</text>
  <text class="brand-name brand-name--side" x="93" y="400" text-anchor="middle">NOVA ROOT</text>
  <text class="product-title" x="497" y="388" text-anchor="middle" textLength="525" lengthAdjust="spacingAndGlyphs">RUNE MOSA</text>
  <text class="slogan" x="493" y="457" text-anchor="middle">ALL-IN-ONE PREMIUM PROTEIN</text>
  <text class="slogan" x="493" y="486" text-anchor="middle">NUTRITIONAL SHAKE</text>
  <rect x="363" y="493" width="259" height="27" fill="var(--label-white)"/>
  <text class="slogan slogan--boxed" x="492" y="515" text-anchor="middle">FOR BLACK WOMEN</text>
  <text class="protein-type" x="488" y="592" text-anchor="middle">WHEY PROTEIN</text>
  <text class="net-weight" x="492" y="738" text-anchor="middle">750g</text>
  <text class="band-text" transform="translate(792,545) rotate(-52.8)" text-anchor="middle">THIS IS OUR MEAL REPLACEMENT</text>
  <text class="flavour-name" transform="translate(972,520) rotate(-90)" text-anchor="middle">strawberry banana</text>
</svg>

<!-- Vanilla -->
<svg class="label label--vanilla" viewBox="0 0 988 760" xmlns="http://www.w3.org/2000/svg">
  <defs>
    <linearGradient id="topfade-v" x1="0" y1="0" x2="0" y2="1"><stop offset="0.4" stop-color="#fff"/><stop offset="0.78" stop-color="#000"/></linearGradient>
    <linearGradient id="arm-v" gradientUnits="userSpaceOnUse" x1="988" y1="110" x2="520" y2="745"><stop offset="0" stop-color="#111"/><stop offset="0.5" stop-color="#fff"/></linearGradient>
    <linearGradient id="fig-v" x1="0" y1="0" x2="1" y2="1"><stop offset="0" stop-color="#555"/><stop offset="0.5" stop-color="#111"/><stop offset="1" stop-color="#333"/></linearGradient>
    <linearGradient id="flav-v" x1="0" y1="0" x2="0" y2="1"><stop offset="0.3" stop-color="#c9c9c9"/><stop offset="0.6" stop-color="#f3e6a6"/><stop offset="0.9" stop-color="#e9cf6a"/><stop offset="1" stop-color="#6b4a2a"/></linearGradient>
  </defs>
  <rect width="988" height="760" fill="var(--label-black)"/>
  <polygon points="267,0 720,0 494,470" fill="url(#topfade-v)"/>
  <rect x="0" y="0" width="180" height="760" fill="url(#fig-v)" role="img" aria-label="Silhouette of a woman"/>
  <rect x="446" y="210" width="58" height="80" rx="10" fill="#0a0a0a" role="img" aria-label="Small figure silhouette"/>
  <polygon points="570,760 988,208 988,760" fill="var(--panel-grey)"/>
  <polygon points="660,760 988,330 988,760" fill="url(#flav-v)" role="img" aria-label="Vanilla shake splash with vanilla flower and pods"/>
  <polygon points="570,760 988,208 988,318 650,760" fill="var(--vanilla)"/>
  <polygon class="w-shape" points="182,398 235,380 418,665 460,608 494,650 530,608 570,665 988,113 988,208 570,760 558,760 494,640 430,760 415,760" fill="url(#arm-v)"/>
  <text class="brand-name" x="494" y="170" text-anchor="middle">NOVA ROOT</text>
  <text class="brand-name brand-name--side" x="93" y="400" text-anchor="middle">NOVA ROOT</text>
  <text class="product-title" x="497" y="388" text-anchor="middle" textLength="525" lengthAdjust="spacingAndGlyphs">RUNE MOSA</text>
  <text class="slogan" x="493" y="457" text-anchor="middle">ALL-IN-ONE PREMIUM PROTEIN</text>
  <text class="slogan" x="493" y="486" text-anchor="middle">NUTRITIONAL SHAKE</text>
  <rect x="363" y="493" width="259" height="27" fill="var(--label-white)"/>
  <text class="slogan slogan--boxed" x="492" y="515" text-anchor="middle">FOR BLACK WOMEN</text>
  <text class="protein-type" x="488" y="592" text-anchor="middle">WHEY PROTEIN</text>
  <text class="net-weight" x="492" y="738" text-anchor="middle">750g</text>
  <text class="band-text" transform="translate(792,545) rotate(-52.8)" text-anchor="middle">THIS IS OUR MEAL REPLACEMENT</text>
  <text class="flavour-name" transform="translate(972,525) rotate(-90)" text-anchor="middle">Vanilla</text>
</svg>

</body>
</html>
```